Design and Renovation Company Luxury Business Card

I want to create a luxury business card for a Design and Renovation Firm . We will use our current logo. The company name is 528BUILDA. We do not want anything standard. We need a very unique concept.
Please see uploaded inspiration. I really like the textured paper option. I would like the card to be thick with debossing, and/or embossing options. The logo has orange in it but I would like to see the card with and without the orange. I think the orange may make the company feel less high-end. The goal is to elevate the logo not match its vibe per se of the logo. We want something very unique, not standard at all!
I would like a space for :
Logo,
Name,
Position,
Email,
Office number,
Website Address,
Business Address,
Thank you!
Have fun!
Target Market(s)
Home owners Age 35 +
Industry/Entity Type
Design and Renovation
Contact Information for Business Card
Logo, Name, Position, Email, Office number, Website Address, Business Address,.
Colors
Designer to choose colors to be used in the design.
Requirements
Must have
- A luxury designer feel. Must be black or dark grey but open to other luxury ideas.
Nice to have
- Gold, silver, black embossing or debossing. Textured paper design.
Should not have
- A cheap look and feel.

```html
<!DOCTYPE html>
<html lang="en">
<head>
<meta charset="utf-8">
<title>528BUILDA Business Card</title>
<link href="https://fonts.googleapis.com/css2?family=Poppins:wght@400;500;600;700&display=swap" rel="stylesheet">
<style>
  :root {
    --backdrop: #e3e7e8;
    --card: #202124;
    --card-deep: #141517;
    --ink-light: #ffffff;
    --tile-glow: #e8e8e8;
    --tile-mid: #55575b;
  }
  * { margin: 0; padding: 0; box-sizing: border-box; }
  html, body {
    width: 1200px; height: 960px; overflow: hidden;
    background: var(--backdrop);
    font-family: "Poppins", sans-serif;
  }
  .card {
    position: absolute; left: 250px; width: 701px; height: 400px;
    background: var(--card); overflow: hidden;
  }
  .card-front { top: 60px; }
  .card-back { top: 500px; }

  .front-texture {
    position: absolute; inset: 0;
    background:
      radial-gradient(ellipse 70% 60% at 100% 0%, var(--tile-glow) 0%, rgba(200,200,200,0.55) 30%, rgba(85,87,91,0.35) 60%, rgba(32,33,36,0) 85%),
      linear-gradient(180deg, #2a2b2e 0%, var(--card) 45%, var(--card-deep) 100%);
  }
  .front-brand {
    position: absolute; left: 582px; top: 283px; width: 46px;
    display: flex; flex-direction: column; align-items: center; gap: 4px;
  }
  .front-brand-square { width: 22px; height: 22px; background: var(--ink-light); }
  .front-brand-name {
    color: var(--ink-light); font-size: 7.5px; font-weight: 500;
    letter-spacing: 0.6px; white-space: nowrap;
  }

  .back-brand-name {
    position: absolute; left: 58px; top: 205px;
    transform: translate(-50%, -50%) rotate(-90deg);
    font-size: 50px; font-weight: 700; color: var(--card-deep);
    letter-spacing: 1px; white-space: nowrap; line-height: 1;
  }
  .back-brand-square {
    position: absolute; left: 30px; top: 318px;
    width: 56px; height: 56px; background: var(--card-deep);
  }

  .accent-bar {
    position: absolute; right: 0; top: 149px; width: 21px; height: 50px;
    background: var(--ink-light);
  }
  .contact-block {
    position: absolute; right: 29px; top: 0; text-align: right;
    color: var(--ink-light);
  }
  .person-name {
    position: absolute; right: 0; top: 140px; white-space: nowrap;
    font-size: 36px; line-height: 1; letter-spacing: 0.5px;
  }
  .person-name .first { font-weight: 700; }
  .person-name .last { font-weight: 400; }
  .person-role {
    position: absolute; right: 0; top: 180px; white-space: nowrap;
    font-size: 17px; font-weight: 600; letter-spacing: 0.4px;
  }
  .address {
    position: absolute; right: 0; top: 224px; white-space: nowrap;
    font-size: 18px; line-height: 26px; letter-spacing: 0.5px;
  }
  .contact-list {
    position: absolute; right: 0; top: 300px; list-style: none;
  }
  .contact-list li {
    display: flex; justify-content: flex-end; align-items: center;
    gap: 12px; height: 26px; font-size: 18px; letter-spacing: 0.5px;
    white-space: nowrap;
  }
  .contact-list svg { width: 16px; height: 16px; flex: none; }
</style>
</head>
<body>
  <section class="card card-front">
    <div class="front-texture" role="img" aria-label="Grid pattern of small square tiles fading from dark charcoal to bright silver toward the top right"></div>
    <div class="front-brand">
      <span class="front-brand-square"></span>
      <span class="front-brand-name">528BUILDA</span>
    </div>
  </section>

  <section class="card card-back">
    <div class="back-brand-name">528BUILDA</div>
    <span class="back-brand-square"></span>

    <span class="accent-bar"></span>
    <div class="contact-block">
      <h1 class="person-name"><span class="first">Marta</span> <span class="last">Kovaric</span></h1>
      <p class="person-role">Founder &amp; CEO</p>
      <p class="address">4170 Aldergrove Rd. Suite 120<br>Cedar Hill, TX 75104</p>
      <ul class="contact-list">
        <li>(555) 214-0637
          <svg viewBox="0 0 16 16" aria-hidden="true"><path d="M4 1.5l2.3 2.8-1.4 1.6c.8 1.9 2.2 3.3 4.2 4.2l1.6-1.4 2.8 2.3-1.4 2.2C7.5 13 3 8.5 1.8 2.9z" fill="#fff"/></svg>
        </li>
        <li>info@yourwebsite.com
          <svg viewBox="0 0 16 16" aria-hidden="true"><circle cx="8" cy="8" r="6.5" fill="none" stroke="#fff" stroke-width="1.4"/><path d="M1.5 8h13M8 1.5c-2.4 2.2-2.4 10.8 0 13M8 1.5c2.4 2.2 2.4 10.8 0 13" fill="none" stroke="#fff" stroke-width="1.2"/></svg>
        </li>
        <li>www.yourwebsite.com
          <svg viewBox="0 0 16 16" aria-hidden="true"><path d="M1.5 6.5L8 2l6.5 4.5V14h-13z" fill="none" stroke="#fff" stroke-width="1.4"/><path d="M1.5 6.5L8 10.5l6.5-4" fill="none" stroke="#fff" stroke-width="1.4"/></svg>
        </li>
      </ul>
    </div>
  </section>
</body>
</html>
```